Financial Advisor Resource Firm needs business card design

Need business card design for company in Omaha NE called Meridale Circle. We provide resources to financial advisors....workshop programs, retirement analysis, and insurance planning. I would like to see designs that use grays, greens, black, and white colors. The final design should communicate 'collaboration' and be simple yet attractive to financial planning clients. I will attached our logo and another picture of a puzzle piece coming together. I would like the incorporate the puzzle picture somehow, maybe on the back somehow, with color or just the gray scale....OR, the picture be the front of the card with 'Meridale' definition on it (see upload) and then company logo, employee name, title, address on the back (see ppt uploaded). The following disclosure needs to be included somewhere- Advisory services offered through Stonebrook Assets, LLC.
Updates

I uploaded a svg and ai file of the logo

Target Market(s)

Financial planning clients and financial advisors....so pretty diverse age range of about 40-70.

Industry/Entity Type

Financial Planning

Contact Information for Business Card

Tobias L. Fenwright, MBA
Founder/President
5287 E. Larkin Road
Suite 230
Omaha, NE 68190
Phone- (402) 555-0147
Cell- (402) 555-0183
Fax- (402) 555-0129
email- tobias@meridaleplan.example
web address- www.meridaleplan.example

Colors
1b1b1b
474747
d3d3d3
ffffff
9bcb3c
abd036

Requirements
Must have
• Must include logo provided, must be 2 sided, and must have disclosure...all of these items listed in project description

```html
<!DOCTYPE html>
<html lang="en">
<head>
<meta charset="utf-8">
<title>Meridale Circle — Business Card</title>
<link rel="stylesheet" href="https://fonts.googleapis.com/css2?family=Ubuntu:wght@400;500&display=swap">
<style>
  :root {
    --ink: #1b1b1b;
    --charcoal: #474747;
    --silver: #d3d3d3;
    --paper: #ffffff;
    --green: #9bcb3c;
    --lime: #abd036;
    --backdrop: #f3f3f3;
    --mist: #eeeeee;
  }
  * { margin: 0; padding: 0; box-sizing: border-box; }
  html, body {
    width: 1200px; height: 900px; overflow: hidden;
    background: var(--backdrop);
    font-family: "Ubuntu", sans-serif;
  }
  .canvas { position: relative; width: 1200px; height: 900px; }
  .card {
    position: absolute; width: 611px; height: 348px; overflow: hidden;
    box-shadow: 0 14px 28px rgba(0,0,0,0.18);
  }
  .card-front { left: 294px; top: 90px; background: var(--ink); }
  .card-back { left: 293px; top: 483px; background: var(--paper); }

  .wordmark { position: absolute; display: flex; align-items: center; gap: 9px; }
  .wordmark-dot { width: 14px; height: 14px; border-radius: 50%; background: var(--green); }
  .wordmark-name { font-size: 27px; font-weight: 500; letter-spacing: 0.5px; white-space: nowrap; }
  .card-front .wordmark { left: 36px; top: 138px; }
  .card-front .wordmark-name { color: var(--paper); }
  .card-back .wordmark { left: 37px; top: 60px; }
  .card-back .wordmark-name { color: var(--charcoal); }

  .tagline {
    position: absolute; left: 30px; top: 193px; width: 245px;
    text-align: center; color: var(--paper); font-size: 16px; line-height: 19px;
    white-space: nowrap;
  }
  .photo-blob { position: absolute; left: 0; top: 0; }

  .backdrop-circle {
    position: absolute; left: 392px; top: 142px; width: 190px; height: 190px;
    border-radius: 50%; background: var(--mist);
  }
  .identity { position: absolute; right: 37px; top: 48px; text-align: right; }
  .person-name { color: var(--green); font-size: 21px; font-weight: 500; white-space: nowrap; }
  .person-name .credential { color: var(--charcoal); font-size: 15px; font-weight: 400; margin-left: 5px; }
  .person-title { color: var(--charcoal); font-size: 16px; margin-top: 1px; }
  .address { color: var(--green); font-size: 16px; line-height: 19px; margin-top: 10px; }
  .accent-tab { position: absolute; right: 0; top: 56px; width: 11px; height: 30px; background: var(--green); }

  .contact-list { position: absolute; left: 37px; top: 202px; list-style: none; }
  .contact-list li {
    display: flex; align-items: center; height: 26px;
    color: var(--charcoal); font-size: 16px;
  }
  .contact-list svg { width: 16px; height: 16px; margin-right: 13px; fill: var(--green); }
  .website {
    position: absolute; right: 37px; top: 283px;
    color: var(--charcoal); font-size: 16px;
  }
  .website .domain { color: var(--green); }
  .disclosure {
    position: absolute; left: 37px; bottom: 12px;
    color: var(--charcoal); font-size: 10px; letter-spacing: 0.2px;
  }
</style>
</head>
<body>
<main class="canvas">

  <section class="card card-front" aria-label="Card front">
    <div class="wordmark">
      <span class="wordmark-dot"></span>
      <span class="wordmark-name">Meridale Circle</span>
    </div>
    <p class="tagline">To come together and unite<br>in common interest and focus</p>
    <svg class="photo-blob" width="611" height="348" viewBox="0 0 611 348">
      <defs>
        <linearGradient id="photo-tone" x1="0" y1="0" x2="1" y2="1">
          <stop offset="0" stop-color="#d8d8d8"/>
          <stop offset="0.5" stop-color="#9a9a9a"/>
          <stop offset="1" stop-color="#3e3e3e"/>
        </linearGradient>
      </defs>
      <path d="M338 72 C300 100 300 240 330 280 C360 310 450 300 490 270 C420 280 340 270 330 200 C320 140 340 100 380 70 Z" fill="var(--green)"/>
      <path role="img" aria-label="Grayscale photo of hands joining puzzle pieces"
            d="M390 72 C440 55 500 80 545 110 C585 140 580 190 555 225 C530 265 480 295 420 293 C360 290 318 260 315 210 C312 150 340 90 390 72 Z"
            fill="url(#photo-tone)"/>
    </svg>
  </section>

  <section class="card card-back" aria-label="Card back">
    <div class="backdrop-circle" aria-hidden="true"></div>
    <div class="wordmark">
      <span class="wordmark-dot"></span>
      <span class="wordmark-name">Meridale Circle</span>
    </div>
    <div class="identity">
      <p class="person-name">Tobias L. Fenwright<span class="credential">MBA</span></p>
      <p class="person-title">Founder | President</p>
      <p class="address">5287 E. Larkin Road<br>Suite 230, Omaha, NE 68190</p>
    </div>
    <span class="accent-tab"></span>
    <ul class="contact-list">
      <li><svg viewBox="0 0 24 24"><path d="M6.6 10.8a15 15 0 0 0 6.6 6.6l2.2-2.2c.3-.3.7-.4 1-.2 1.1.4 2.3.6 3.6.6.6 0 1 .4 1 1V20c0 .6-.4 1-1 1A17 17 0 0 1 3 4c0-.6.4-1 1-1h3.5c.6 0 1 .4 1 1 0 1.3.2 2.5.6 3.6.1.3 0 .7-.2 1z"/></svg>(402) 555 - 0147</li>
      <li><svg viewBox="0 0 24 24"><path d="M7 1h10a2 2 0 0 1 2 2v18a2 2 0 0 1-2 2H7a2 2 0 0 1-2-2V3a2 2 0 0 1 2-2zm0 3v14h10V4zm5 15.5a1 1 0 1 0 0 2 1 1 0 0 0 0-2z"/></svg>(402) 555 - 0183</li>
      <li><svg viewBox="0 0 24 24"><path d="M3 7h4v14H3zm6-5h8v6h4v13H9zm2 8v2h2v-2zm4 0v2h2v-2zm-4 4v2h2v-2zm4 0v2h2v-2z"/></svg>(402) 555 - 0129</li>
      <li><svg viewBox="0 0 24 24"><path d="M2 5h20v2l-10 6L2 7zm0 4 10 6 10-6v10H2z"/></svg>tobias@meridaleplan.example</li>
    </ul>
    <p class="website">www.<span class="domain">meridaleplan</span>.example</p>
    <p class="disclosure">Advisory services offered through Stonebrook Assets, LLC.</p>
  </section>

</main>
</body>
</html>
```